We need a new brochure design for our dental clinic, Birchvale Dental. We have attached the information we want printed and photos to include.

Industry/Entity Type

Dental

```html
<!DOCTYPE html>
<html lang="en">
<head>
<meta charset="utf-8">
<title>Birchvale Dental Brochure</title>
<link href="https://fonts.googleapis.com/css2?family=Arimo:wght@400;700&family=Pinyon+Script&display=swap" rel="stylesheet">
<style>
  :root {
    --brand-blue: #1f9ad8;
    --brand-blue-text: #1a8fcf;
    --deep-blue: #16557f;
    --pale-blue: #b8dcf2;
    --white: #ffffff;
    --rule: rgba(255,255,255,0.55);
  }
  * { margin: 0; padding: 0; box-sizing: border-box; }
  html, body { width: 1200px; height: 850px; overflow: hidden; background: var(--white); }
  body { font-family: "Arimo", Arial, sans-serif; }
  .brochure { position: relative; width: 1200px; height: 850px; overflow: hidden; }

  /* Left panel */
  .panel-left { position: absolute; left: 0; top: 0; width: 400px; height: 850px; background: var(--white); }
  .intro { position: absolute; left: 32px; top: 32px; width: 350px; font-size: 16.5px; line-height: 22px; color: var(--brand-blue-text); }
  .photo { position: absolute; left: 0; width: 400px; }
  .photo-reception { top: 97px; height: 210px; background: linear-gradient(135deg, #e9e4dc 0%, #f6f4ef 45%, #c9ccc8 100%); }
  .photo-surgery { top: 352px; height: 210px; background: linear-gradient(160deg, #ecebe8 0%, #f4f2ef 40%, #d4485a 70%, #e9e6e2 100%); }
  .photo-corridor { top: 607px; height: 178px; background: linear-gradient(90deg, #a14fc4 0%, #d9a0e6 45%, #f2cdef 55%, #b056c7 100%); }
  .caption { position: absolute; left: 0; width: 400px; background: var(--brand-blue); color: var(--white); font-size: 11px; line-height: 18px; padding: 0 32px; display: flex; align-items: center; }
  .caption-reception { top: 307px; height: 45px; }
  .caption-surgery { top: 562px; height: 45px; }
  .caption-corridor { top: 785px; height: 65px; }

  /* Middle panel */
  .panel-middle { position: absolute; left: 400px; top: 0; width: 400px; height: 850px; background: var(--brand-blue); color: var(--white); }
  .services-title { position: absolute; left: 43px; top: 33px; font-size: 18px; letter-spacing: 0.3px; }
  .services-rule { position: absolute; left: 43px; top: 57px; width: 357px; height: 1px; background: var(--rule); }
  .services-list { position: absolute; left: 44px; top: 66px; list-style: none; }
  .services-list li { position: relative; padding-left: 17px; font-size: 17px; line-height: 29.5px; }
  .services-list li::before { content: ""; position: absolute; left: 0; top: 11px; width: 8px; height: 8px; border-radius: 50%; background: var(--white); }
  .offer { position: absolute; left: 46px; top: 448px; width: 310px; height: 89px; border-top: 1px solid var(--rule); border-bottom: 1px solid var(--rule); color: var(--pale-blue); }
  .offer-rate { position: absolute; left: 0; top: 3px; font-size: 55px; line-height: 60px; }
  .offer-note { position: absolute; left: 4px; top: 58px; font-size: 18.5px; }
  .call-line { position: absolute; left: 0; width: 400px; top: 577px; text-align: center; font-size: 17px; }
  .phone-box { position: absolute; left: 47px; top: 607px; width: 305px; height: 65px; background: var(--white); border-radius: 10px; display: flex; align-items: center; justify-content: center; gap: 8px; }
  .phone-number { color: var(--deep-blue); font-weight: 700; font-size: 36px; letter-spacing: 2px; }
  .address { position: absolute; left: 0; width: 400px; top: 698px; text-align: center; }
  .address-street { font-size: 13px; letter-spacing: 1.5px; line-height: 18px; }
  .address-detail { font-size: 9.5px; letter-spacing: 0.8px; line-height: 16px; }
  .footer-rule { position: absolute; left: 22px; top: 752px; width: 358px; height: 1px; background: var(--rule); }
  .footer-name { position: absolute; left: 45px; top: 776px; display: flex; align-items: center; gap: 7px; font-size: 18px; color: var(--white); }
  .footer-dot { width: 14px; height: 14px; border-radius: 50%; background: var(--white); }
  .footer-contact { position: absolute; left: 235px; top: 774px; font-size: 10px; line-height: 22px; letter-spacing: 0.5px; text-align: left; }
  .footer-contact .tel { padding-left: 53px; }

  /* Right panel */
  .panel-right { position: absolute; left: 800px; top: 0; width: 400px; height: 850px; background: var(--white); }
  .photo-smile { position: absolute; left: 0; top: 0; width: 400px; height: 467px; background: radial-gradient(ellipse at 60% 40%, #f3d2c4 0%, #e9b8a6 45%, #d9ecf5 100%); }
  .tagline { position: absolute; left: 0; top: 480px; width: 400px; height: 170px; color: var(--brand-blue-text); }
  .tagline-script { position: absolute; left: 46px; top: 6px; font-family: "Pinyon Script", cursive; font-size: 64px; line-height: 80px; }
  .tagline-small { position: absolute; left: 42px; top: 85px; font-size: 20px; }
  .tagline-large { position: absolute; left: 174px; top: 95px; font-size: 56px; line-height: 60px; }
  .band { position: absolute; left: 0; top: 655px; width: 400px; height: 33px; background: var(--brand-blue); color: var(--white); font-size: 18px; display: flex; align-items: center; justify-content: center; }
  .brand-mark { position: absolute; left: 140px; top: 728px; display: flex; align-items: center; gap: 10px; color: var(--brand-blue-text); font-size: 28px; }
  .brand-dot { width: 26px; height: 26px; border-radius: 50%; background: var(--brand-blue-text); }
</style>
</head>
<body>
<main class="brochure">

  <section class="panel-left">
    <p class="intro">At Birchvale Dental we believe in investing in state of the art technology to ensure a comfortable dental experience for you.</p>
    <div class="photo photo-reception" role="img" aria-label="Bright clinic reception area with seating and a glass entrance"></div>
    <p class="caption caption-reception">Feel free to relax and ask our friendly staff for some light refreshments before or after your dental treatment</p>
    <div class="photo photo-surgery" role="img" aria-label="Treatment room with red dental chairs and equipment"></div>
    <p class="caption caption-surgery">Our Aurora Treatment Centre provides excellent comfort for our patients with its advanced thermo upholstery and lumbar support.</p>
    <div class="photo photo-corridor" role="img" aria-label="Modern corridor lit in pink and purple light"></div>
    <p class="caption caption-corridor">A unique, comfortable and modern dental experience awaits you.</p>
  </section>

  <section class="panel-middle">
    <h2 class="services-title">SERVICES PROVIDED</h2>
    <div class="services-rule"></div>
    <ul class="services-list">
      <li>Dental Implants</li>
      <li>Clear Aligners</li>
      <li>Smile makeovers</li>
      <li>Dental Orthopaedic Treatment</li>
      <li>Braces for Children &amp; Adults</li>
      <li>Dental fillings &amp; Porcelain restorations</li>
      <li>Gum Treatments</li>
      <li>Root canal Treatments</li>
      <li>Wisdom tooth surgery</li>
      <li>Dentures</li>
      <li>Children’s dentistry</li>
      <li>Digital X-rays</li>
    </ul>
    <div class="offer">
      <p class="offer-rate">0% interest</p>
      <p class="offer-note">free instalment plans available.</p>
    </div>
    <p class="call-line">Call us for an appointment today</p>
    <div class="phone-box">
      <svg width="32" height="32" viewBox="0 0 32 32" aria-hidden="true">
        <path d="M4 12c0-4 5-6 12-6s12 2 12 6v2h-6v-3c-2-1-10-1-12 0v3H4z" fill="#1f9ad8"/>
        <path d="M9 15h14l3 11H6z" fill="#1f9ad8"/>
        <circle cx="16" cy="20" r="3" fill="#fff"/>
      </svg>
      <span class="phone-number">6371 2958</span>
    </div>
    <div class="address">
      <p class="address-street">215 Marlow Lane</p>
      <p class="address-detail">( Opposite Harbourview Mall and Beside Cocoa Corner)</p>
      <p class="address-detail">Singapore - 418 352</p>
    </div>
    <div class="footer-rule"></div>
    <div class="footer-name"><span class="footer-dot"></span>Birchvale Dental</div>
    <div class="footer-contact">
      <p class="tel">Tel : 6371 2958</p>
      <p>info@birchvaledental.com.sg</p>
    </div>
  </section>

  <section class="panel-right">
    <div class="photo-smile" role="img" aria-label="Close-up of a bright, healthy smile"></div>
    <div class="tagline">
      <p class="tagline-script">Feel great</p>
      <p class="tagline-small">about your</p>
      <p class="tagline-large">Smile</p>
    </div>
    <p class="band">A healthier smile for a healthier you</p>
    <div class="brand-mark"><span class="brand-dot"></span>Birchvale Dental</div>
  </section>

</main>
</body>
</html>
```